RW Holloway LLC Business Card - Civil Engineering & Consulting Firm

We need a Business Card that is elegant, and masculine.  It is our Professional Civil Engineering & Consulting Company located in San Antonio TX (Not s construction or builder firm- no gears & no tool images please). We provide civil engineering services including  commercial site plans, grading and drainage plans, utility plans, hydraulics and hydrology, land planning, utility coordination, and other general civil engineering services related to commercial and residential development.
We have 2 existing Logos. We would like to convey reliability, strength, trustworthiness and attention to detail.  Blues and orange tones as per logo We are OK with the use of a darker blue in the mix.  We have 2 logo versions - Full Company Name Logo to go on the back of card, & Small Icon Logo for the front w/ personal Info.

Target Market(s)
Architects, Real Estate Developers, Other Strctural Engineers, Surveyers, General Contractors
Industry/Entity Type
Professional Civil Engineering
Contact Information for Business Card
Name, Position, Address, Cell & Office #, email, and company website
Font styles to use
Other font styles liked:
- Avian
Requirements
Should not have
- No Tools, No Gears, no Cranes, or Construction Equipment.

```html
<!DOCTYPE html>
<html lang="en">
<head>
<meta charset="utf-8">
<title>RW Holloway LLC Business Card</title>
<link href="https://fonts.googleapis.com/css2?family=Josefin+Sans:wght@300;400&family=Arimo:wght@400&display=swap" rel="stylesheet">
<style>
  :root {
    --backdrop: #2b2521;
    --card: #0d0d0d;
    --sky: #7fb0da;
    --blue: #0a72e6;
    --orange: #f4962a;
    --white: #f4f4f4;
  }
  * { margin: 0; padding: 0; box-sizing: border-box; }
  html, body { width: 1200px; height: 842px; overflow: hidden; background: var(--backdrop); }
  .canvas { position: relative; width: 1200px; height: 842px; }
  .card {
    position: absolute; top: 266px; width: 540px; height: 309px;
    background: var(--card); overflow: hidden;
  }
  .card--contact { left: 40px; }
  .card--brand { left: 620px; }

  .band { position: absolute; left: 0; width: 100%; }
  .band--top { top: 0; height: 14px; background: var(--sky); border-bottom: 4px solid var(--orange); height: 18px; }
  .band--bottom { bottom: 0; height: 18px; background: var(--sky); border-top: 4px solid var(--orange); }

  .contact {
    position: absolute; left: 0; right: 0; top: 58px; text-align: center;
    font-family: "Arimo", Arial, sans-serif; color: var(--white);
  }
  .contact__name { font-family: "Josefin Sans", sans-serif; font-weight: 400; font-size: 24px; letter-spacing: 0.5px; color: var(--sky); line-height: 1; }
  .contact__name span { color: var(--orange); }
  .contact__role { font-size: 12px; color: var(--orange); letter-spacing: 0.5px; margin-top: 3px; }
  .rule { width: 64px; height: 1px; background: var(--white); margin: 14px auto; }
  .contact__line { font-size: 14px; line-height: 19px; }

  .marker { position: absolute; display: flex; }
  .marker__block { width: 40px; height: 68px; background: var(--blue); }
  .marker__stripe { width: 5px; height: 68px; background: var(--orange); }
  .marker--left { left: 0; top: 150px; }
  .marker--right { right: 0; top: 60px; flex-direction: row-reverse; }
  .marker--right .marker__block { width: 34px; height: 52px; }
  .marker--right .marker__stripe { height: 52px; margin-right: 6px; }
  .marker--left .marker__stripe { margin-left: 6px; }

  .brand { position: absolute; left: 110px; top: 100px; width: 340px; text-align: center; }
  .brand__name { font-family: "Josefin Sans", sans-serif; font-weight: 300; font-size: 40px; letter-spacing: 3px; color: var(--sky); line-height: 1; }
  .brand__rule { height: 1px; background: var(--sky); margin: 10px 10px 8px; }
  .brand__tagline { font-family: "Josefin Sans", sans-serif; font-weight: 400; font-size: 11px; letter-spacing: 5px; color: var(--orange); }
</style>
</head>
<body>
<main class="canvas">
  <section class="card card--contact">
    <div class="band band--top"></div>
    <div class="contact">
      <p class="contact__name">DANIEL <span>MERCER</span></p>
      <p class="contact__role">MANAGING DIRECTOR</p>
      <div class="rule"></div>
      <p class="contact__line">044-210 387 654</p>
      <p class="contact__line">hello@rwholloway.com</p>
      <p class="contact__line">www.rwholloway.com</p>
      <div class="rule"></div>
      <p class="contact__line">421, Address line goes here</p>
      <p class="contact__line">45452, Country Name</p>
    </div>
    <div class="band band--bottom"></div>
  </section>

  <section class="card card--brand">
    <div class="marker marker--right"><div class="marker__block"></div><div class="marker__stripe"></div></div>
    <div class="brand">
      <p class="brand__name">RW HOLLOWAY LLC</p>
      <div class="brand__rule"></div>
      <p class="brand__tagline">CONSULTING ENGINEERS</p>
    </div>
    <div class="marker marker--left"><div class="marker__block"></div><div class="marker__stripe"></div></div>
  </section>
</main>
</body>
</html>
```